UX Design for Analytics Web Application

http://velqoranthe.com/
We are tech & consulting company with analytics products (web applications), located at Rio de Janeiro, Brazil.

We are searching a partner do develop UX for our products, i.e, aesthetics, usability, HTML/CSS.

Currently we have a product suite and the goal is to make a pilot re-design project with one of our products.

The product of interest is interactive webapp that aims at data analysis, significantly different from blogs, e-commerce or landing pages.

We do have a software development team but we lack an UX & HTML expert. Currently we use Bootstrap templates but the results are insatisfatory.

So, the project scope is, to develop the arts (UX, aesthetics, etc) along with the code/mockup (HTML/CSS) for one of our product (3 pages).

This is a pilot project and there's potential to rehire for our other products. Code quality is of importance.

More details and specification can be found in attached files.

Target Market(s)

Executives, managers & consultants

Industry/Entity Type

It Company

Coding

Coded - Design and coding required

Number of Pages Required

3 page

Font styles to use
Sans Serif

Requirements
Must have
• (see attached files, prefer the pptx version))
• -Responsive
Nice to have
• (see attached files, prefer the pptx version)
Should not have
• -Avoid Green, Red and Yellow colors. They have a meaning of good, bad and average in our products.

```html
<!DOCTYPE html>
<html lang="en">
<head>
<meta charset="utf-8">
<title>Velqor — Process Dashboard</title>
<link rel="stylesheet" href="https://fonts.googleapis.com/css2?family=Open+Sans:wght@400;600;700&display=swap">
<style>
:root{
  --teal:#2bb3c8;
  --teal-tab:#35bdd2;
  --purple:#9b55e0;
  --purple-soft:#c48cf0;
  --grey-ring:#dcdcdc;
  --navy-top:#233a70;
  --navy-low:#1e2c58;
  --feed-bg:#1b2236;
  --feed-item:#3b4761;
  --card-bg:#eeeeee;
  --ink:#222;
  --line:#e2e2e2;
  --footer:#e9e9e9;
  --cyan-name:#3fd0e8;
}
*{box-sizing:border-box;margin:0;padding:0}
html,body{width:981px;height:1200px;overflow:hidden}
body{font-family:'Open Sans',sans-serif;background:#fff;color:var(--ink);position:relative}

.topbar{position:absolute;left:0;top:0;width:981px;height:105px;border-bottom:2px solid var(--line)}
.menu-toggle{position:absolute;left:20px;top:43px;width:22px}
.menu-toggle span{display:block;height:4px;background:#222;margin-bottom:4px;border-radius:1px}
.brand{position:absolute;left:108px;top:24px;display:flex;align-items:center;gap:10px}
.brand-dot{width:40px;height:40px;border-radius:50%;background:#333}
.brand-name{font-size:44px;font-weight:700;color:#333;line-height:50px;letter-spacing:-1px}
.top-actions{position:absolute;right:110px;top:36px;display:flex;gap:26px}
.round-btn{width:33px;height:33px;border-radius:50%;background:#262626;display:flex;align-items:center;justify-content:center;position:relative}
.round-btn .count{position:absolute;left:-8px;top:-6px;width:16px;height:16px;border-radius:50%;background:#3cb6ec;color:#fff;font-size:8px;line-height:16px;text-align:center}

.stats{position:absolute;left:108px;top:119px;width:376px;height:314px;color:#fff}
.stats-top{height:170px;background:var(--navy-top);position:relative}
.stats-count{position:absolute;left:20px;top:32px;font-size:92px;font-weight:700;line-height:92px;letter-spacing:-3px}
.stats-label{position:absolute;left:21px;top:113px;font-size:20px}
.stats-ring{position:absolute;left:248px;top:20px}
.stats-done{position:absolute;left:232px;top:118px;font-size:14px;white-space:nowrap}
.stats-done b{font-size:27px;margin-right:6px}
.stats-low{height:144px;background:var(--navy-low);position:relative;padding:22px 0 0 27px}
.stat-row{display:flex;align-items:center;height:34px}
.stat-row p{width:207px;font-size:16px}
.stat-row p b{font-size:25px;margin-right:4px}
.stat-row:first-child{height:38px}
.bar{height:12px}
.bar-teal{width:116px;background:var(--teal)}
.bar-purple{width:50px;background:var(--purple)}
.bar-grey{width:37px;background:#ddd}
.stat-row em{font-style:normal;font-weight:700;font-size:13px;margin-left:8px}

.feed{position:absolute;left:108px;top:446px;width:376px;height:314px;background:var(--feed-bg);padding:13px 13px 0}
.feed-item{display:flex;height:72px;background:var(--feed-item);margin-bottom:7px}
.feed-thumb{width:69px;flex:none}
.feed-text{padding:14px 12px 0 15px;font-size:11px;line-height:15px;color:#fff}
.feed-text .who{color:var(--cyan-name)}
.feed-text .proc{color:var(--purple-soft)}
.feed-text time{display:block;font-size:8.5px;color:#b8c0cc;margin-top:4px}
.feed-more{display:block;width:66px;height:34px;margin:18px auto 0;border:1px solid #5c6479;color:#c9ced8;font-size:11px;line-height:32px;text-align:center}

.toolbar{position:absolute;left:497px;top:119px;width:375px;height:42px;border-bottom:3px solid var(--teal-tab);display:flex;gap:3px}
.tool{width:92px;height:37px;background:#e6e6e6;color:#555;font-size:11.5px;display:flex;align-items:center;justify-content:center;gap:5px}
.tool.is-active{background:var(--teal-tab);color:#fff}

.cards{position:absolute;left:497px;top:172px;display:grid;grid-template-columns:182px 182px;column-gap:12px;row-gap:13px}
.card{width:182px;height:183px;background:var(--card-bg);position:relative}
.card-media{height:85px;position:relative}
.card-title{position:absolute;left:0;bottom:0;width:100%;height:22px;background:rgba(20,20,28,.5);color:#fff;font-size:10.5px;font-weight:700;line-height:22px;padding-left:14px}
.card-flag{position:absolute;right:0;top:0;width:18px;height:18px;display:flex;align-items:center;justify-content:center}
.flag-teal{background:var(--teal)}
.flag-purple{background:var(--purple)}
.flag-dark{background:rgba(0,0,0,.35)}
.card-metric{position:absolute;left:14px;top:102px;font-size:10px;line-height:12px;color:#222;width:95px;padding-left:13px}
.card-metric svg{position:absolute;left:0;top:1px}
.card-note{position:absolute;left:14px;top:136px;font-size:8px;line-height:12px;color:#666;width:100px}
.card-ring{position:absolute;left:113px;top:105px}

.footer{position:absolute;left:0;top:1154px;width:981px;height:46px;background:var(--footer);font-size:9px;color:#333;text-align:center;line-height:46px}
.footer .page-code{position:absolute;right:10px;top:10px;font-size:9px;color:#555;line-height:12px}
</style>
</head>
<body>

<header class="topbar">
  <div class="menu-toggle"><span></span><span></span><span></span></div>
  <div class="brand">
    <div class="brand-dot"></div>
    <div class="brand-name">Velqor</div>
  </div>
  <div class="top-actions">
    <div class="round-btn"><span class="count">0</span>
      <svg width="14" height="14" viewBox="0 0 14 14"><path d="M7 1a4 4 0 0 0-4 4v3L1.5 10h11L11 8V5a4 4 0 0 0-4-4zM5.5 11a1.5 1.5 0 0 0 3 0z" fill="#fff"/></svg>
    </div>
    <div class="round-btn">
      <svg width="12" height="12" viewBox="0 0 12 12"><circle cx="6" cy="3.5" r="2.8" fill="#fff"/><path d="M1 12a5 4.5 0 0 1 10 0z" fill="#fff"/></svg>
    </div>
    <div class="round-btn">
      <svg width="14" height="14" viewBox="0 0 14 14"><circle cx="7" cy="7" r="4.5" fill="none" stroke="#fff" stroke-width="3" stroke-dasharray="2.2 1.3"/><circle cx="7" cy="7" r="2.5" fill="none" stroke="#fff" stroke-width="1.5"/></svg>
    </div>
  </div>
</header>

<section class="stats">
  <div class="stats-top">
    <div class="stats-count">14</div>
    <div class="stats-label">Active Processes</div>
    <svg class="stats-ring" width="92" height="92" viewBox="0 0 92 92">
      <g transform="rotate(-90 46 46)" fill="none" stroke-width="12">
        <circle cx="46" cy="46" r="40" stroke="var(--grey-ring)"/>
        <circle cx="46" cy="46" r="40" stroke="var(--purple)" pathLength="100" stroke-dasharray="92 100"/>
        <circle cx="46" cy="46" r="40" stroke="var(--teal)" pathLength="100" stroke-dasharray="72 100"/>
      </g>
    </svg>
    <div class="stats-done"><b>72%</b>Concluded</div>
  </div>
  <div class="stats-low">
    <div class="stat-row"><p><b>31</b>Millions Expent</p><span class="bar bar-teal"></span></div>
    <div class="stat-row"><p>With 2 Millions of gap</p><span class="bar bar-purple"></span><em>6%</em></div>
    <div class="stat-row"><p>and 1.5 million negotiated</p><span class="bar bar-grey"></span><em>5%</em></div>
  </div>
</section>

<section class="feed">
  <article class="feed-item">
    <div class="feed-thumb" role="img" aria-label="Tablet showing a 3D bar chart" style="background:linear-gradient(160deg,#f4f7fb,#c9d6ea 60%,#7fa0cf)"></div>
    <div class="feed-text"><span class="who">Tomas Reyl</span> upload new data with 23823 rows to the <span class="proc">XPTO Process</span> and he is happy now<time>2 days ago</time></div>
  </article>
  <article class="feed-item">
    <div class="feed-thumb" role="img" aria-label="Hand pointing at a rising growth graph" style="background:linear-gradient(135deg,#2c3d57,#6f8fb3 55%,#a9bfd6)"></div>
    <div class="feed-text"><span class="who">Mira Okon</span> Donec non eros sodales tristique<time>2 days ago</time></div>
  </article>
  <article class="feed-item">
    <div class="feed-thumb" role="img" aria-label="Magnifying glass over blue data charts" style="background:linear-gradient(135deg,#8fd0ee,#3a74c8 60%,#1d3f8f)"></div>
    <div class="feed-text"><span class="who">Caio Lenner</span> Integer cursus justo orci, lacinia ultrices nisi elementum vitae<time>2 days ago</time></div>
  </article>
  <a class="feed-more">Sell All</a>
</section>

<nav class="toolbar">
  <div class="tool is-active"><svg width="10" height="10" viewBox="0 0 10 10"><circle cx="4" cy="4" r="3" fill="none" stroke="#fff" stroke-width="1.6"/><path d="M6.2 6.2 9 9" stroke="#fff" stroke-width="1.8"/></svg>Search</div>
  <div class="tool"><svg width="11" height="9" viewBox="0 0 11 9"><path d="M0 1h2M3 1h8M0 4.5h2M3 4.5h8M0 8h2M3 8h8" stroke="#555" stroke-width="1.6"/></svg>Sort by</div>
  <div class="tool"><svg width="9" height="9" viewBox="0 0 9 9"><path d="M0 0h9L5.5 4v5L3.5 8V4z" fill="#555"/></svg>Filter by</div>
  <div class="tool"><svg width="10" height="10" viewBox="0 0 10 10"><circle cx="5" cy="5" r="5" fill="#555"/><path d="M5 2.5v5M2.5 5h5" stroke="#fff" stroke-width="1.5"/></svg>Add Process</div>
</nav>

<main class="cards">
  <article class="card">
    <div class="card-media" role="img" aria-label="Team working at laptops on a desk" style="background:linear-gradient(135deg,#6b5e52,#b9ad9f 50%,#4a4540)"><span class="card-flag flag-teal"><svg width="10" height="10" viewBox="0 0 10 10"><circle cx="5" cy="5" r="4" fill="none" stroke="#fff" stroke-width="1.3"/><path d="M3 5l1.5 1.5L7 3.8" fill="none" stroke="#fff" stroke-width="1.3"/></svg></span><div class="card-title">PROCESS BY DONUT</div></div>
    <p class="card-metric"><svg width="9" height="10" viewBox="0 0 9 10"><path d="M4.5 0 9 4.5H6V10H3V4.5H0z" fill="#26324f"/></svg>14 million in expenses</p>
    <p class="card-note">Nulla a ultricies, malesua­da rhoncus eget. Suspen­disse erat, dictum.</p>
    <svg class="card-ring" width="60" height="60" viewBox="0 0 60 60"><g transform="rotate(-90 30 30)" fill="none" stroke-width="8"><circle cx="30" cy="30" r="25" stroke="var(--grey-ring)"/><circle cx="30" cy="30" r="25" stroke="var(--purple)" pathLength="100" stroke-dasharray="92 100"/><circle cx="30" cy="30" r="25" stroke="var(--teal)" pathLength="100" stroke-dasharray="72 100"/></g></svg>
  </article>
  <article class="card">
    <div class="card-media" role="img" aria-label="Printed pie and bar charts on a desk" style="background:linear-gradient(135deg,#e9ecf1,#b8c4d6 50%,#7b8699)"><span class="card-flag flag-purple"><svg width="10" height="10" viewBox="0 0 10 10"><circle cx="5" cy="5" r="3.2" fill="none" stroke="#fff" stroke-width="2" stroke-dasharray="1.6 1"/></svg></span><div class="card-title">PROCESS BY DONUT</div></div>
    <p class="card-metric"><svg width="9" height="10" viewBox="0 0 9 10"><path d="M4.5 0 9 4.5H6V10H3V4.5H0z" fill="#26324f"/></svg>14 million in expenses</p>
    <p class="card-note">Nulla a ultricies, malesua­da rhoncus eget. Suspen­disse erat, dictum.</p>
    <svg class="card-ring" width="60" height="60" viewBox="0 0 60 60"><g transform="rotate(-90 30 30)" fill="none" stroke-width="8"><circle cx="30" cy="30" r="25" stroke="var(--grey-ring)"/><circle cx="30" cy="30" r="25" stroke="var(--purple)" pathLength="100" stroke-dasharray="92 100"/><circle cx="30" cy="30" r="25" stroke="var(--teal)" pathLength="100" stroke-dasharray="72 100"/></g></svg>
  </article>
  <article class="card">
    <div class="card-media" role="img" aria-label="Hands reviewing colourful charts" style="background:linear-gradient(135deg,#3c4a5c,#c9d3df 55%,#e9edf2)"><span class="card-flag flag-purple"><svg width="10" height="10" viewBox="0 0 10 10"><circle cx="5" cy="5" r="3.2" fill="none" stroke="#fff" stroke-width="2" stroke-dasharray="1.6 1"/></svg></span><div class="card-title">PROCESS BY DONUT</div></div>
    <p class="card-metric"><svg width="9" height="10" viewBox="0 0 9 10"><path d="M4.5 0 9 4.5H6V10H3V4.5H0z" fill="#26324f"/></svg>14 million in expenses</p>
    <p class="card-note">Nulla a ultricies, malesua­da rhoncus eget. Suspen­disse erat, dictum.</p>
    <svg class="card-ring" width="60" height="60" viewBox="0 0 60 60"><g transform="rotate(-90 30 30)" fill="none" stroke-width="8"><circle cx="30" cy="30" r="25" stroke="var(--grey-ring)"/><circle cx="30" cy="30" r="25" stroke="var(--purple)" pathLength="100" stroke-dasharray="92 100"/><circle cx="30" cy="30" r="25" stroke="var(--teal)" pathLength="100" stroke-dasharray="72 100"/></g></svg>
  </article>
  <article class="card">
    <div class="card-media" role="img" aria-label="Hands holding a tablet with a dashboard" style="background:linear-gradient(135deg,#efe9df,#a89d8c 55%,#3d3833)"><span class="card-flag flag-dark"><svg width="10" height="10" viewBox="0 0 10 10"><circle cx="5" cy="5" r="4" fill="none" stroke="#fff" stroke-width="1.3"/><path d="M2.3 7.7l5.4-5.4" stroke="#fff" stroke-width="1.3"/></svg></span><div class="card-title">PROCESS BY DONUT</div></div>
    <p class="card-metric"><svg width="9" height="10" viewBox="0 0 9 10"><path d="M4.5 0 9 4.5H6V10H3V4.5H0z" fill="#26324f"/></svg>14 million in expenses</p>
    <p class="card-note">Nulla a ultricies, malesua­da rhoncus eget. Suspen­disse erat, dictum.</p>
    <svg class="card-ring" width="60" height="60" viewBox="0 0 60 60"><g transform="rotate(-90 30 30)" fill="none" stroke-width="8"><circle cx="30" cy="30" r="25" stroke="var(--grey-ring)"/><circle cx="30" cy="30" r="25" stroke="var(--purple)" pathLength="100" stroke-dasharray="92 100"/><circle cx="30" cy="30" r="25" stroke="var(--teal)" pathLength="100" stroke-dasharray="72 100"/></g></svg>
  </article>
  <article class="card">
    <div class="card-media" role="img" aria-label="Hands holding a tablet with area and donut charts" style="background:linear-gradient(135deg,#1e2530,#52627a 55%,#1a1f28)"><span class="card-flag flag-teal"><svg width="10" height="10" viewBox="0 0 10 10"><circle cx="5" cy="5" r="4" fill="none" stroke="#fff" stroke-width="1.3"/><path d="M3 5l1.5 1.5L7 3.8" fill="none" stroke="#fff" stroke-width="1.3"/></svg></span><div class="card-title">PROCESS BY DONUT</div></div>
    <p class="card-metric"><svg width="9" height="10" viewBox="0 0 9 10"><path d="M4.5 0 9 4.5H6V10H3V4.5H0z" fill="#26324f"/></svg>14 million in expenses</p>
    <p class="card-note">Nulla a ultricies, malesua­da rhoncus eget. Suspen­disse erat, dictum.</p>
    <svg class="card-ring" width="60" height="60" viewBox="0 0 60 60"><g transform="rotate(-90 30 30)" fill="none" stroke-width="8"><circle cx="30" cy="30" r="25" stroke="var(--grey-ring)"/><circle cx="30" cy="30" r="25" stroke="var(--purple)" pathLength="100" stroke-dasharray="92 100"/><circle cx="30" cy="30" r="25" stroke="var(--teal)" pathLength="100" stroke-dasharray="72 100"/></g></svg>
  </article>
  <article class="card">
    <div class="card-media" role="img" aria-label="Group of business people standing together" style="background:linear-gradient(135deg,#e6e6e6,#8a8a8f 50%,#2e2e35)"><span class="card-flag flag-purple"><svg width="10" height="10" viewBox="0 0 10 10"><circle cx="5" cy="5" r="3.2" fill="none" stroke="#fff" stroke-width="2" stroke-dasharray="1.6 1"/></svg></span><div class="card-title">PROCESS BY DONUT</div></div>
    <p class="card-metric"><svg width="9" height="10" viewBox="0 0 9 10"><path d="M4.5 0 9 4.5H6V10H3V4.5H0z" fill="#26324f"/></svg>14 million in expenses</p>
    <p class="card-note">Nulla a ultricies, malesua­da rhoncus eget. Suspen­disse erat, dictum.</p>
    <svg class="card-ring" width="60" height="60" viewBox="0 0 60 60"><g transform="rotate(-90 30 30)" fill="none" stroke-width="8"><circle cx="30" cy="30" r="25" stroke="var(--grey-ring)"/><circle cx="30" cy="30" r="25" stroke="var(--purple)" pathLength="100" stroke-dasharray="92 100"/><circle cx="30" cy="30" r="25" stroke="var(--teal)" pathLength="100" stroke-dasharray="72 100"/></g></svg>
  </article>
  <article class="card">
    <div class="card-media" role="img" aria-label="Magnifying glass over a blue data map" style="background:linear-gradient(135deg,#bfe1f7,#4b8fd6 55%,#1c4a9a)"><span class="card-flag flag-dark"><svg width="10" height="10" viewBox="0 0 10 10"><circle cx="5" cy="5" r="4" fill="none" stroke="#fff" stroke-width="1.3"/><path d="M2.3 7.7l5.4-5.4" stroke="#fff" stroke-width="1.3"/></svg></span><div class="card-title">PROCESS BY DONUT</div></div>
    <p class="card-metric"><svg width="9" height="10" viewBox="0 0 9 10"><path d="M4.5 0 9 4.5H6V10H3V4.5H0z" fill="#26324f"/></svg>14 million in expenses</p>
    <p class="card-note">Nulla a ultricies, malesua­da rhoncus eget. Suspen­disse erat, dictum.</p>
    <svg class="card-ring" width="60" height="60" viewBox="0 0 60 60"><g transform="rotate(-90 30 30)" fill="none" stroke-width="8"><circle cx="30" cy="30" r="25" stroke="var(--grey-ring)"/><circle cx="30" cy="30" r="25" stroke="var(--purple)" pathLength="100" stroke-dasharray="92 100"/><circle cx="30" cy="30" r="25" stroke="var(--teal)" pathLength="100" stroke-dasharray="72 100"/></g></svg>
  </article>
  <article class="card">
    <div class="card-media" role="img" aria-label="Business people reviewing documents with a phone" style="background:linear-gradient(135deg,#2a2a2e,#8c8a86 55%,#d9d6cf)"><span class="card-flag flag-teal"><svg width="10" height="10" viewBox="0 0 10 10"><circle cx="5" cy="5" r="4" fill="none" stroke="#fff" stroke-width="1.3"/><path d="M3 5l1.5 1.5L7 3.8" fill="none" stroke="#fff" stroke-width="1.3"/></svg></span><div class="card-title">PROCESS BY DONUT</div></div>
    <p class="card-metric"><svg width="9" height="10" viewBox="0 0 9 10"><path d="M4.5 0 9 4.5H6V10H3V4.5H0z" fill="#26324f"/></svg>14 million in expenses</p>
    <p class="card-note">Nulla a ultricies, malesua­da rhoncus eget. Suspen­disse erat, dictum.</p>
    <svg class="card-ring" width="60" height="60" viewBox="0 0 60 60"><g transform="rotate(-90 30 30)" fill="none" stroke-width="8"><circle cx="30" cy="30" r="25" stroke="var(--grey-ring)"/><circle cx="30" cy="30" r="25" stroke="var(--purple)" pathLength="100" stroke-dasharray="92 100"/><circle cx="30" cy="30" r="25" stroke="var(--teal)" pathLength="100" stroke-dasharray="72 100"/></g></svg>
  </article>
  <article class="card">
    <div class="card-media" role="img" aria-label="Laptop showing a stock chart in an office" style="background:linear-gradient(135deg,#d8dadc,#7d858c 55%,#3b4046)"><span class="card-flag flag-teal"><svg width="10" height="10" viewBox="0 0 10 10"><circle cx="5" cy="5" r="4" fill="none" stroke="#fff" stroke-width="1.3"/><path d="M3 5l1.5 1.5L7 3.8" fill="none" stroke="#fff" stroke-width="1.3"/></svg></span><div class="card-title">PROCESS BY DONUT</div></div>
    <p class="card-metric"><svg width="9" height="10" viewBox="0 0 9 10"><path d="M4.5 0 9 4.5H6V10H3V4.5H0z" fill="#26324f"/></svg>14 million in expenses</p>
    <p class="card-note">Nulla a ultricies, malesua­da rhoncus eget. Suspen­disse erat, dictum.</p>
    <svg class="card-ring" width="60" height="60" viewBox="0 0 60 60"><g transform="rotate(-90 30 30)" fill="none" stroke-width="8"><circle cx="30" cy="30" r="25" stroke="var(--grey-ring)"/><circle cx="30" cy="30" r="25" stroke="var(--purple)" pathLength="100" stroke-dasharray="92 100"/><circle cx="30" cy="30" r="25" stroke="var(--teal)" pathLength="100" stroke-dasharray="72 100"/></g></svg>
  </article>
  <article class="card">
    <div class="card-media" role="img" aria-label="Glasses resting on printed blue bar charts" style="background:linear-gradient(135deg,#3d5a80,#8fb3da 55%,#2b4f8c)"><span class="card-flag flag-teal"><svg width="10" height="10" viewBox="0 0 10 10"><circle cx="5" cy="5" r="4" fill="none" stroke="#fff" stroke-width="1.3"/><path d="M3 5l1.5 1.5L7 3.8" fill="none" stroke="#fff" stroke-width="1.3"/></svg></span><div class="card-title">PROCESS BY DONUT</div></div>
    <p class="card-metric"><svg width="9" height="10" viewBox="0 0 9 10"><path d="M4.5 0 9 4.5H6V10H3V4.5H0z" fill="#26324f"/></svg>14 million in expenses</p>
    <p class="card-note">Nulla a ultricies, malesua­da rhoncus eget. Suspen­disse erat, dictum.</p>
    <svg class="card-ring" width="60" height="60" viewBox="0 0 60 60"><g transform="rotate(-90 30 30)" fill="none" stroke-width="8"><circle cx="30" cy="30" r="25" stroke="var(--grey-ring)"/><circle cx="30" cy="30" r="25" stroke="var(--purple)" pathLength="100" stroke-dasharray="92 100"/><circle cx="30" cy="30" r="25" stroke="var(--teal)" pathLength="100" stroke-dasharray="72 100"/></g></svg>
  </article>
</main>

<footer class="footer">Copyright © 2017 Company name. All rights reserved.<span class="page-code">M2</span></footer>

</body>
</html>
```